Web Developer Needs a Business Card Design

I need a personal business card design that represents me as a web developer for potential employers. I would like the background to be a dark color on the front for contrast with my logo and name. The back will have all my information along with a smaller version of the logo. I want something with a modern look and feel, not too conservative. This will be used for potential employers and freelance work.

Industry/Entity Type

Business

Contact Information for Business Card

Front should have my logo and name. The back should have all my personal information which would include: name: Tom Varulek, phone: 570-614-3098, email: tomvarulek@quillbox.net, website url: www.tomvarulek.net, logo, web developer.

Font styles to use
Sans Serif

Requirements
Must have
• Must include my logo. The color palette base color will be the logo color.

```html
<!DOCTYPE html>
<html lang="en">
<head>
<meta charset="utf-8">
<title>Tom Varulek — Business Card</title>
<link rel="stylesheet" href="https://fonts.googleapis.com/css2?family=Open+Sans:wght@400;600&display=swap">
<style>
  :root {
    --canvas-bg: #3a3330;
    --card-bg: #050505;
    --brand-teal: #5fc4b0;
    --text-white: #ffffff;
    --icon-ink: #050505;
  }
  * { margin: 0; padding: 0; box-sizing: border-box; }
  html, body {
    width: 1200px; height: 780px; overflow: hidden;
    background: var(--canvas-bg);
    font-family: "Open Sans", Arial, sans-serif;
    color: var(--text-white);
  }
  .stage {
    position: relative; width: 1200px; height: 780px;
    display: flex; align-items: center; justify-content: center; gap: 40px;
  }
  .card {
    position: relative; width: 540px; height: 309px;
    background: var(--card-bg);
    border-radius: 3px;
    box-shadow: 0 10px 24px rgba(0,0,0,.45);
  }
  .brand-ring {
    position: absolute; border-radius: 50%;
    border: 10px solid var(--brand-teal);
  }
  /* Front */
  .card-front .brand-ring { width: 150px; height: 150px; left: 195px; top: 34px; }
  .card-front .holder-name {
    position: absolute; left: 150px; top: 196px;
    font-size: 36px; font-weight: 400; letter-spacing: .5px;
  }
  /* Back */
  .card-back .brand-ring { width: 158px; height: 158px; left: 42px; top: 72px; }
  .divider {
    position: absolute; left: 238px; top: 36px; width: 3px; height: 240px;
    background: var(--text-white);
  }
  .identity { position: absolute; left: 262px; top: 78px; }
  .identity .holder-name { font-size: 34px; font-weight: 400; line-height: 1; letter-spacing: .5px; }
  .identity .role { font-size: 15px; margin-top: 4px; }
  .contact-list { position: absolute; left: 262px; top: 176px; list-style: none; }
  .contact-list li {
    display: flex; align-items: center; gap: 10px;
    font-size: 17px; line-height: 1; margin-bottom: 10px;
  }
  .contact-icon { width: 15px; height: 15px; flex: none; }
</style>
</head>
<body>
<main class="stage">
  <section class="card card-front" aria-label="Card front">
    <div class="brand-ring" aria-hidden="true"></div>
    <h1 class="holder-name">Tom Varulek</h1>
  </section>

  <section class="card card-back" aria-label="Card back">
    <div class="brand-ring" aria-hidden="true"></div>
    <div class="divider" aria-hidden="true"></div>
    <div class="identity">
      <h2 class="holder-name">Tom Varulek</h2>
      <p class="role">web developer</p>
    </div>
    <ul class="contact-list">
      <li>
        <svg class="contact-icon" viewBox="0 0 16 16" aria-hidden="true">
          <rect width="16" height="16" rx="2" fill="var(--text-white)"/>
          <path d="M5 3.5 L7 6 L6 7.2 Q7 9.5 8.8 10 L10 9 L12.5 11 L11.2 12.6 Q6 12.5 3.6 5 Z" fill="var(--icon-ink)"/>
        </svg>
        <span>570-614-3098</span>
      </li>
      <li>
        <svg class="contact-icon" viewBox="0 0 16 16" aria-hidden="true">
          <rect width="16" height="16" rx="2" fill="var(--text-white)"/>
          <circle cx="8" cy="8" r="4.8" fill="none" stroke="var(--icon-ink)" stroke-width="1.3"/>
          <path d="M3.2 8 H12.8 M8 3.2 Q5.5 8 8 12.8 M8 3.2 Q10.5 8 8 12.8" fill="none" stroke="var(--icon-ink)" stroke-width="1"/>
        </svg>
        <span>www.tomvarulek.net,</span>
      </li>
      <li>
        <svg class="contact-icon" viewBox="0 0 16 16" aria-hidden="true">
          <rect width="16" height="16" rx="2" fill="var(--text-white)"/>
          <rect x="3" y="4.5" width="10" height="7" fill="none" stroke="var(--icon-ink)" stroke-width="1.2"/>
          <path d="M3 4.5 L8 8.8 L13 4.5" fill="none" stroke="var(--icon-ink)" stroke-width="1.2"/>
        </svg>
        <span>tomvarulek@quillbox.net</span>
      </li>
    </ul>
  </section>
</main>
</body>
</html>
```